Bluefinch Painting needs a Website

We need a website built for a Painting company I own, we mainly do residential painting, but don't want to be limited to that.

Need to have estimate request form.
Need pic's of past projects

I like the look of the website for http://www.harbor-brushworks.com
& "Westlake Home inspections"

My logo that was designed here on ArtHatch on the front page

I would like one of the houses I downloaded as part of the background
of the front page.

Target Market(s)

Home owners

Industry/Entity Type

Painting

Number of Pages Required

1 page

Font styles to use
Serif

Requirements
Must have
• Estimate request form for home owners to fill out -
• Name:
• Phone Number:
• Address:
• E-mail:
• Painting project description:
• And my info to:
• My phone number: (555) 318-7046
• My web address bluefinchpainting.example
Nice to have
• My logo that was designed here on ArtHatch

```html
<!DOCTYPE html>
<html lang="en">
<head>
<meta charset="utf-8">
<title>Bluefinch Painting</title>
<link rel="stylesheet" href="https://fonts.googleapis.com/css2?family=Tinos:wght@400;700&family=Arimo:wght@400;700&family=Open+Sans:wght@400;600&family=Mako&display=swap">
<style>
:root{
  --navy:#1b2436;
  --navy-2:#2a344a;
  --brand-blue:#2a87c8;
  --title-blue:#2a73b3;
  --button-blue:#2b9be0;
  --light-grey:#e9e9e9;
  --card-bg:#f8f8f8;
  --card-line:#d6d6d6;
  --ink:#1d1d1d;
  --band:#111214;
  --footer:#333335;
  --footer-panel:#222224;
  --muted:#8a8a8a;
  --white:#ffffff;
}
*{box-sizing:border-box;margin:0;padding:0}
html,body{width:1200px;height:2413px;overflow:hidden}
body{position:relative;background:var(--white);font-family:"Arimo",Arial,sans-serif;color:var(--ink)}
h1,h2,h4{font-weight:400}
.abs{position:absolute}

/* Header */
.site-header{left:0;top:0;width:1200px;height:100px;background:linear-gradient(180deg,var(--navy-2),var(--navy))}
.brand-plate{left:113px;top:0;width:394px;height:100px;background:var(--white);clip-path:polygon(8% 0,100% 0,92% 100%,0 100%)}
.brand{left:166px;top:34px;display:flex;align-items:center;gap:10px;white-space:nowrap}
.brand-square{width:30px;height:30px;background:var(--title-blue)}
.brand-name{font-family:"Tinos",serif;font-size:23px;color:var(--title-blue);letter-spacing:.5px}
.main-nav{left:515px;top:49px;display:flex;gap:22px;font-size:13px;font-weight:700;color:var(--white)}
.main-nav span.sep{font-weight:400}
.header-phone{left:920px;top:16px;font-size:22px;font-weight:700;color:var(--white)}
.social{left:910px;top:53px;display:flex;gap:14px}
.social i{display:block;height:22px;background:#3d5a98}
.social i.like{width:58px;background:#4a67a8}
.social i.sq{width:22px}
.social i.red{background:#d34836}
.social i.cyan{background:#39a9e0}

/* Hero */
.hero{left:0;top:100px;width:1200px;height:521px;background:linear-gradient(180deg,#7fb2e0 0%,#9cc3df 18%,#4f5a66 45%,#5c7047 70%,#b5b2aa 100%)}
.hero-box{left:277px;top:241px;width:420px;height:161px;background:rgba(42,135,200,.85);padding:36px 14px 0}
.hero-box h1{font-size:28px;font-weight:700;color:var(--white);margin-bottom:14px}
.hero-box p{font-size:13px;line-height:21px;color:var(--white)}

/* About */
.about-title{left:0;top:656px;width:1200px;text-align:center;font-family:"Tinos",serif;font-size:32px;color:var(--title-blue)}
.about-text{left:170px;top:716px;width:860px;text-align:center;font-size:12.5px;line-height:21px}
.about-text p+p{margin-top:19px}

/* Quote + video */
.quote-panel{left:0;top:873px;width:512px;height:430px;background:var(--brand-blue)}
.how-panel{left:512px;top:873px;width:688px;height:430px;background:var(--light-grey)}
.quote-title{left:161px;top:912px;font-family:"Tinos",serif;font-size:29px;color:var(--ink)}
.field{left:161px;width:280px;height:34px;background:var(--white);font-size:12px;color:#9a9a9a;padding:9px 8px}
.field.comment{height:56px}
.submit{left:161px;top:1231px;width:280px;height:37px;background:#151515;color:var(--white);font-family:"Mako","Open Sans",sans-serif;font-size:18px;text-align:center;line-height:37px}
.how-title{left:568px;top:912px;font-family:"Tinos",serif;font-size:29px;color:var(--title-blue)}
.video{left:568px;top:962px;width:482px;height:254px;background:linear-gradient(180deg,#9fbbd6 0%,#d8dbdc 35%,#f2f2f2 70%,#6c6f70 100%)}
.play{left:779px;top:1041px;width:64px;height:64px}
.how-text{left:568px;top:1234px;width:500px;font-size:12.5px;line-height:20px}

/* Project cards */
.card{width:277px;height:302px;top:1488px;background:var(--card-bg);border:1px solid var(--card-line);text-align:center;padding:150px 16px 0}
.card-photo{width:184px;height:184px;border-radius:50%;top:1399px;border:4px solid #ececec;box-shadow:0 1px 3px rgba(0,0,0,.2)}
.card h3{font-family:"Tinos",serif;font-size:16px;font-weight:700;letter-spacing:1px;margin-bottom:6px}
.card p{font-size:12.5px;line-height:19px;margin-bottom:10px}
.read-more{display:inline-block;width:84px;height:26px;line-height:26px;background:var(--button-blue);color:var(--white);font-size:12.5px;font-weight:700;border-radius:3px}

/* CTA band */
.cta{left:0;top:1874px;width:1200px;height:98px;background:var(--band)}
.cta-text{left:161px;top:1902px;font-family:"Mako","Open Sans",sans-serif;font-size:28px;color:var(--white)}
.cta-button{left:870px;top:1898px;width:166px;height:47px;background:var(--button-blue);border-radius:3px;color:var(--white);font-family:"Mako","Open Sans",sans-serif;font-size:21px;font-weight:700;text-align:center;line-height:47px;box-shadow:0 3px 0 #1a6ea5}

/* Footer */
.footer{left:0;top:1972px;width:1200px;height:402px;background:var(--footer);border-top:1px solid #555}
.footer-brand{left:158px;top:2012px;display:flex;align-items:center;gap:8px;white-space:nowrap}
.footer-brand .brand-square{width:24px;height:24px;background:var(--white)}
.footer-brand .brand-name{font-size:17px;color:var(--white)}
.footer-about{left:168px;top:2078px;width:220px;font-family:"Open Sans",sans-serif;font-size:11px;line-height:16px;color:var(--white)}
.contact-line{left:178px;display:flex;align-items:center;gap:14px;font-family:"Open Sans",sans-serif;font-size:13px;color:var(--white)}
.contact-line.email{color:var(--button-blue)}
.col-title{top:2032px;font-family:"Mako","Open Sans",sans-serif;font-size:13px;letter-spacing:.5px;color:#3a9ad8}
.news-item{left:430px;width:290px;height:77px;border-bottom:1px solid #444;display:flex;gap:22px;padding-top:14px}
.news-date{width:40px;height:42px;background:#242426;text-align:center;color:#3a9ad8;font-family:"Open Sans",sans-serif;font-size:13px;line-height:18px;padding-top:4px}
.news-date small{display:block;font-size:8px;color:var(--muted);line-height:10px}
.news-item p{font-family:"Open Sans",sans-serif;font-size:11.5px;line-height:18px;color:var(--muted);width:210px}
.tweets{left:759px;top:2067px;width:303px;height:249px;background:var(--footer-panel);padding:40px 28px 0}
.tweet-dot{left:767px;top:2057px;width:24px;height:24px;border-radius:50%;background:#3a9ad8}
.tweet p{font-family:"Open Sans",sans-serif;font-size:11.5px;line-height:16px;color:var(--muted)}
.tweet .tag{display:block;margin-top:12px;padding-bottom:6px;border-bottom:1px solid #3a3a3a;color:#3a9ad8;font-size:13px;font-family:"Open Sans",sans-serif}
.tweet+.tweet{margin-top:16px}
.more-tweets{left:950px;top:2293px;font-family:"Open Sans",sans-serif;font-size:11px;font-style:italic;color:#3a9ad8}
.to-top{left:1033px;top:2333px;width:29px;height:24px}

.copyright-bar{left:0;top:2374px;width:1200px;height:39px;background:var(--brand-blue);text-align:center;line-height:39px;font-size:12.5px;color:var(--ink)}
</style>
</head>
<body>

<header class="abs site-header"></header>
<div class="abs brand-plate"></div>
<div class="abs brand"><span class="brand-square"></span><span class="brand-name">BLUEFINCH PAINTING</span></div>
<nav class="abs main-nav"><span>HOME</span><span class="sep">/</span><span>SERVICES</span><span class="sep">/</span><span>ABOUT</span><span class="sep">/</span><span>CONTACT</span></nav>
<div class="abs header-phone">(123) 456 2919</div>
<div class="abs social"><i class="like"></i><i class="sq red"></i><i class="sq cyan"></i></div>

<section class="abs hero" role="img" aria-label="Photo of a freshly painted grey craftsman house with a garage and green garden"></section>
<div class="abs hero-box">
  <h1>BLUEFINCH PAINTING</h1>
  <p>We offer Interior and Exterior House Painting throughout the Eastside and Greater Seattle area.</p>
</div>

<h2 class="abs about-title">ABOUT BLUEFINCH PAINTING</h2>
<div class="abs about-text">
  <p>simply dummy text of the printing and typesetting industry. Lorem Ipsum has been the industry's standard dummy text ever since the 1500s, when an unknown printer took a galley of type and scrambled it to make a type specimen book. It has survived not only five centuries, but also the leap into electronic typesetting, remaining essentially unchanged. It was popularised in the 1960s with the release of Typeline sheets.</p>
  <p>containing Lorem Ipsum passages, and more recently with desktop publishing software like Quillset Layout including versions of Lorem Ipsum.</p>
</div>

<section class="abs quote-panel"></section>
<section class="abs how-panel"></section>
<h2 class="abs quote-title">GET QUOTE</h2>
<div class="abs field" style="top:965px">Your Name</div>
<div class="abs field" style="top:1012px">Last Name</div>
<div class="abs field" style="top:1060px">Email Address</div>
<div class="abs field" style="top:1108px">Phone Number</div>
<div class="abs field comment" style="top:1156px">Comment</div>
<div class="abs submit">Submit Now</div>

<h2 class="abs how-title">HOW IT WORK</h2>
<div class="abs video" role="img" aria-label="Video still of the company work trailer parked in front of a house"></div>
<svg class="abs play" viewBox="0 0 64 64" aria-hidden="true"><circle cx="32" cy="32" r="30" fill="#111" stroke="#fff" stroke-width="3"/><path d="M25 19 L47 32 L25 45 Z" fill="#fff"/></svg>
<p class="abs how-text">Lorem ipsum dolor sit amet, consectetur adipiscing elit, sed do eiusmod tempor incididunt ut labore et dolore magna aliqua.</p>

<article class="abs card" style="left:143px"><h3>LOREM IPSUM DOLOR</h3><p>Sed ut perspiciatis unde omnis iste natus error sit voluptatem accusantium dolorem que laudantium voluptatem</p><span class="read-more">Read More</span></article>
<article class="abs card" style="left:462px"><h3>LOREM IPSUM DOLOR</h3><p>Sed ut perspiciatis unde omnis iste natus error sit voluptatem accusantium dolorem que laudantium voluptatem</p><span class="read-more">Read More</span></article>
<article class="abs card" style="left:778px;padding-top:140px"><h3>LOREM IPSUM DOLOR</h3><p>Sed ut perspiciatis unde omnis iste natus error sit voluptatem accusantium dolorem que laudantium voluptatem</p><span class="read-more">Read More</span></article>
<div class="abs card-photo" style="left:191px;background:linear-gradient(180deg,#8fa3b8,#6b6f6a 60%,#4b5a3c)" role="img" aria-label="Past project: painted two-storey house with porch"></div>
<div class="abs card-photo" style="left:505px;background:linear-gradient(180deg,#9dbad8,#8a8478 50%,#3f3f3f)" role="img" aria-label="Past project: house with work truck and trailer in the driveway"></div>
<div class="abs card-photo" style="left:826px;background:linear-gradient(180deg,#a9c1d8,#f0f0f0 45%,#dcdcdc 80%,#555)" role="img" aria-label="Company work trailer parked on a street"></div>

<section class="abs cta"></section>
<div class="abs cta-text">Residential and commercial hauling services in Colorado</div>
<div class="abs cta-button">Get Started</div>

<footer class="abs footer"></footer>
<div class="abs footer-brand"><span class="brand-square"></span><span class="brand-name">BLUEFINCH PAINTING</span></div>
<p class="abs footer-about">Lorem ipsum dolor sit amet, consectetur adipiscing elit, sed do eiusmod tempor incididunt ut labore et dolore magna aliqua. Ut enim ad minim veniam, quis nostrud exercitation ullamco laboris nisi ut aliquip ex ea commodo consequat. Duis aute irure dolor in reprehenderit in voluptate velit esse cillum dolore eu</p>
<div class="abs contact-line" style="top:2240px"><svg width="12" height="20" viewBox="0 0 12 20" aria-hidden="true"><rect x="1" y="1" width="10" height="18" rx="2" fill="none" stroke="#2b9be0" stroke-width="2"/><circle cx="6" cy="15.5" r="1.3" fill="#2b9be0"/></svg><span>800.555.1212</span></div>
<div class="abs contact-line email" style="top:2271px"><svg width="16" height="12" viewBox="0 0 16 12" aria-hidden="true"><rect width="16" height="12" rx="1" fill="#2b9be0"/><path d="M1 1 L8 7 L15 1" fill="none" stroke="#333" stroke-width="1.5"/></svg><span>info@ridgecarthauling.example</span></div>

<h4 class="abs col-title" style="left:443px">LATEST NEWS</h4>
<div class="abs news-item" style="top:2062px"><div class="news-date">16<small>JUL</small></div><p>Mauris non mattis libero. Curabitur pellentesque massa vitae…</p></div>
<div class="abs news-item" style="top:2139px"><div class="news-date">12<small>JUL</small></div><p>Mauris non mattis libero. Curabitur pellentesque massa vitae…</p></div>
<div class="abs news-item" style="top:2216px"><div class="news-date">08<small>JUL</small></div><p>Mauris non mattis libero. Curabitur pellentesque massa vitae…</p></div>

<h4 class="abs col-title" style="left:760px">RECENT TWEETS</h4>
<div class="abs tweets">
  <div class="tweet"><p>Mauris non mattis libero. Curabitur pellentesque, massa vitae adipiscing lobortis, odio mauris etum convallis.</p><span class="tag">#confia</span></div>
  <div class="tweet"><p>Mauris non mattis libero. Curabitur pellentesque, massa vitae adipiscing lobortis, odio mauris etum convallis.</p><span class="tag">#confia</span></div>
</div>
<div class="abs tweet-dot"></div>
<div class="abs more-tweets">more tweets ▸</div>
<svg class="abs to-top" viewBox="0 0 29 24" aria-hidden="true"><rect width="29" height="24" fill="#555"/><path d="M9 15 L14.5 9 L20 15" fill="none" stroke="#ddd" stroke-width="2"/></svg>

<div class="abs copyright-bar">Copyright © 2014 All Rights Reserved | Privacy Policy</div>

</body>
</html>
```